Velvet Lantern rebranding my business with a new business card

I have my new logo and now I need a refresher on my business cards. I really want something fun and fresh. I like black background or anything to make the color pop.
Logo
Name: Velvet Lantern
Contact Info as stated below:
Mira Pellow
555-013-4762
Logo
Name: Velvet Lantern
Mira Pellow
555-013-4762
fb.me/VelvetLanternbyMira
Instagram: @VelvetLanternbyMira

Industry/Entity Type

Business

Contact Information for Business Card

double-sided. Logo on one side. Contact info on the other.

Requirements
Must have
• Logo
• Name: Velvet Lantern
• Contact Info as stated below:
• Mira Pellow
• 555-013-4762
• fb.me/VelvetLanternbyMira
• fb.me/VelvetLanternbyMira

```html
<!DOCTYPE html>
<html lang="en">
<head>
<meta charset="utf-8">
<title>Velvet Lantern – Business Card</title>
<link href="https://fonts.googleapis.com/css2?family=Oswald:wght@500&family=Work+Sans:wght@400&display=swap" rel="stylesheet">
<style>
  :root {
    --stage: #2a2a2a;
    --card: #1c1c1d;
    --card-sheen: #262628;
    --teal: #3cc9b0;
    --pink: #e58fae;
    --ink: #f2f2f2;
  }
  * { box-sizing: border-box; margin: 0; padding: 0; }
  html, body {
    width: 1200px; height: 930px; overflow: hidden;
    background: var(--stage);
  }
  .stage {
    width: 1200px; height: 930px;
    display: flex; flex-direction: column;
    align-items: center; justify-content: center;
    gap: 44px;
  }
  .card {
    position: relative;
    width: 700px; height: 400px;
    border-radius: 22px;
    background: linear-gradient(160deg, var(--card-sheen) 0%, var(--card) 55%);
    border-bottom: 7px solid var(--teal);
    box-shadow: 0 14px 30px rgba(0,0,0,.45);
    display: flex; align-items: center; justify-content: center;
  }
  .logo-wordmark {
    font-family: "Oswald", sans-serif;
    font-weight: 500;
    font-size: 46px;
    letter-spacing: 2px;
    color: var(--teal);
    text-transform: uppercase;
  }
  .contact-block { display: flex; align-items: center; gap: 22px; }
  .identity { text-align: right; }
  .identity-name {
    font-family: "Oswald", sans-serif;
    font-weight: 500;
    font-size: 40px;
    letter-spacing: 1.5px;
    color: var(--teal);
    line-height: 1;
  }
  .identity-role {
    font-family: "Work Sans", sans-serif;
    font-size: 15px;
    color: var(--ink);
    margin-top: 4px;
  }
  .divider { width: 2px; height: 92px; background: var(--pink); }
  .details { list-style: none; display: flex; flex-direction: column; gap: 8px; }
  .details li {
    display: flex; align-items: center; gap: 12px;
    font-family: "Work Sans", sans-serif;
    font-size: 17px; color: var(--ink);
  }
  .details svg { width: 14px; height: 14px; flex: none; }
</style>
</head>
<body>
<main class="stage">
  <section class="card card-front" aria-label="Card front">
    <span class="logo-wordmark">Velvet Lantern</span>
  </section>

  <section class="card card-back" aria-label="Card back">
    <div class="contact-block">
      <div class="identity">
        <p class="identity-name">MIRA PELLOW</p>
        <p class="identity-role">Owner</p>
      </div>
      <div class="divider"></div>
      <ul class="details">
        <li>
          <svg viewBox="0 0 14 14" aria-hidden="true"><rect x="3" y="1" width="8" height="12" rx="1.5" fill="none" stroke="#3cc9b0" stroke-width="1.5"/></svg>
          555-013-4762
        </li>
        <li>
          <svg viewBox="0 0 14 14" aria-hidden="true"><rect x="1" y="3" width="12" height="8" fill="#3cc9b0"/><path d="M1 3 L7 8 L13 3" fill="none" stroke="#1c1c1d" stroke-width="1.2"/></svg>
          info@mirapellow.com
        </li>
        <li>
          <svg viewBox="0 0 14 14" aria-hidden="true"><rect x="1.5" y="1.5" width="11" height="11" rx="2" fill="#3cc9b0"/></svg>
          fb.me/VelvetLanternbyMira
        </li>
      </ul>
    </div>
  </section>
</main>
</body>
</html>
```